Stationery Design Project

I need a stationary design for our company. we are based in Houston, TX and we are called Mira Vell Lending. And we are wanting to brand our MoneyMendPlus program, which includes our tax preparation and restoration, credit repair service. Although our business offers other programs, we are interested in mainly focusing on The MoneyMendPlus program. We are looking for way to brand our ourselves and I believe that a great stationery design will help in achieving this goal. Our logo design is blue and light blue. the slogan is orange.

Industry/Entity Type

Business

Requirements
Must have
• Address: 30871 Calloway Ln. B-22
Houston, TX 75419
Tel. 555-318-6207
Fax 555-294-7153
www.miravelllending.example
info@miravelllending.example
Our Slogan: Confidence, Rebuilt!

```html
<!DOCTYPE html>
<html lang="en">
<head>
<meta charset="utf-8">
<title>Mira Vell Lending – Business Card Set</title>
<link href="https://fonts.googleapis.com/css2?family=Marcellus+SC&family=Tinos&family=Didact+Gothic&family=Questrial&display=swap" rel="stylesheet">
<style>
  :root {
    --backdrop: #6b4630;
    --label: #111111;
    --card-white: #ffffff;
    --navy: #123f66;
    --navy-deep: #0f3a60;
    --brand-blue: #1b5f98;
    --sky: #2a9ad6;
    --light-blue: #bfe0f2;
    --orange: #f0952a;
    --text-dark: #222222;
  }
  * { margin: 0; padding: 0; box-sizing: border-box; }
  html, body { width: 1200px; height: 800px; overflow: hidden; }
  body { background: var(--backdrop); position: relative; font-family: "Questrial", sans-serif; }

  .side-label {
    position: absolute; width: 510px; text-align: center;
    font-family: "Questrial", sans-serif; font-size: 21px; color: var(--label);
  }
  .card {
    position: absolute; width: 510px; height: 290px; border-radius: 22px;
    overflow: hidden; box-shadow: 0 6px 14px rgba(0,0,0,.35);
  }
  .card--light { background: var(--card-white); }
  .card--dark { background: var(--navy); }

  .slogan {
    position: absolute; left: 0; width: 100%; text-align: center;
    font-family: "Marcellus SC", serif; font-size: 20px; color: var(--orange); letter-spacing: .5px;
  }
  .website {
    position: absolute; left: 0; width: 100%; text-align: center;
    font-family: "Didact Gothic", sans-serif; font-size: 20px; letter-spacing: 1.6px;
  }
  .card--light .website { color: var(--text-dark); }
  .card--dark .website { color: var(--card-white); }

  .lender-name { font-family: "Tinos", serif; color: var(--card-white); text-align: center; }

  /* Front */
  .front-wave { position: absolute; inset: 0; }
  .program-name {
    position: absolute; left: 40px; top: 98px;
    font-family: "Tinos", serif; font-size: 40px; color: var(--brand-blue);
  }
  .contact-list {
    position: absolute; right: 23px; top: 188px; text-align: right;
    font-family: "Questrial", sans-serif; color: var(--card-white); font-size: 14px; line-height: 18.5px;
  }
  .contact-list b { font-style: italic; }
  .contact-list .address { font-size: 15px; margin-top: 3px; }

  /* Back 1 & 3 framed square */
  .name-square {
    position: absolute; left: 169px; width: 171px; height: 171px;
    display: flex; align-items: flex-end; justify-content: center; padding-bottom: 30px;
  }
  .name-square--navy { background: var(--navy-deep); outline: 1px solid var(--navy-deep); outline-offset: 3px; }
  .name-square--outline { border: 4px solid var(--light-blue); }
  .name-square .lender-name { font-size: 15px; }

  /* Back 2 */
  .mark-square {
    position: absolute; left: 217px; top: 88px; width: 76px; height: 76px;
    border: 2px solid var(--light-blue);
  }
  .lender-name--large { position: absolute; left: 0; width: 100%; top: 200px; font-size: 21px; }
</style>
</head>
<body>

  <div class="side-label" style="left:72px; top:50px;">Front</div>
  <div class="side-label" style="left:621px; top:50px;">Back - 1</div>
  <div class="side-label" style="left:75px; top:410px;">Back - 2</div>
  <div class="side-label" style="left:621px; top:410px;">Back - 3</div>

  <!-- Front -->
  <section class="card card--light card-front" style="left:72px; top:90px;">
    <svg class="front-wave" width="510" height="290" viewBox="0 0 510 290" aria-hidden="true">
      <defs>
        <linearGradient id="waveBlue" x1="0" y1="1" x2="1" y2="0">
          <stop offset="0" stop-color="#1a4f86"/>
          <stop offset="1" stop-color="#1f97d6"/>
        </linearGradient>
      </defs>
      <path d="M0,236 C150,262 290,210 370,160 C430,122 480,108 510,104 L510,290 L0,290 Z" fill="url(#waveBlue)"/>
      <path d="M0,226 C140,250 280,205 360,152 C420,114 470,98 510,96 L510,104 C470,108 428,126 372,162 C290,215 150,262 0,238 Z" fill="#f0952a"/>
      <path d="M0,248 C70,262 140,262 200,250 C140,270 70,272 0,260 Z" fill="#ffffff" opacity=".85"/>
      <path d="M0,262 C70,276 140,276 200,264 L200,290 L0,290 Z" fill="#163f6e" opacity=".55"/>
    </svg>
    <div class="program-name">MoneyMendPlus</div>
    <div class="contact-list">
      <div><b>p</b> : 555-318-6207</div>
      <div><b>f</b> : 555-294-7153</div>
      <div style="margin-top:3px;"><b>e</b> : info@miravelllending.example</div>
      <div><b>w</b> : www.miravelllending.example</div>
      <div class="address">30871 Calloway Ln. B-22, Houston, TX 75419</div>
    </div>
  </section>

  <!-- Back 1 -->
  <section class="card card--light card-back" style="left:621px; top:90px;">
    <div class="slogan" style="top:23px;">Confidence, Rebuilt!</div>
    <div class="name-square name-square--navy" style="top:62px;">
      <div class="lender-name">Mira Vell Lending</div>
    </div>
    <div class="website" style="top:245px;">www.miravelllending.example</div>
  </section>

  <!-- Back 2 -->
  <section class="card card--dark card-back" style="left:75px; top:450px;">
    <div class="slogan" style="top:21px;">Confidence, Rebuilt!</div>
    <div class="mark-square"></div>
    <div class="lender-name lender-name--large">Mira Vell Lending</div>
    <div class="website" style="top:250px;">www.miravelllending.example</div>
  </section>

  <!-- Back 3 -->
  <section class="card card--dark card-back" style="left:621px; top:450px;">
    <div class="slogan" style="top:21px;">Confidence, Rebuilt!</div>
    <div class="name-square name-square--outline" style="top:55px;">
      <div class="lender-name">Mira Vell Lending</div>
    </div>
    <div class="website" style="top:250px;">www.miravelllending.example</div>
  </section>

</body>
</html>
```